Harborline Auto LLC

Car Dealer Customer Service
Address: 2874 Cresthaven Road, Shelbyville, TN 37162
web: www.harborlineautoxq.net
email: harborlineautoxq@mailnest.example
Phone: (931) 555-0148
Phone: (629) 555-0173

```html
<!DOCTYPE html>
<html lang="en">
<head>
<meta charset="UTF-8">
<title>Harborline Auto – Business Cards</title>
<link rel="stylesheet" href="https://fonts.googleapis.com/css2?family=Montserrat:wght@600;800&family=Jost:wght@400;500&display=swap">
<style>
  :root {
    --brand-red: #bb1f24;
    --ink: #1a1a1a;
    --paper: #ffffff;
    --backdrop: #e4e7e3;
    --muted: #444444;
  }
  * { box-sizing: border-box; margin: 0; padding: 0; }
  html, body { width: 1200px; height: 900px; overflow: hidden; }
  body {
    background: var(--backdrop);
    display: flex;
    flex-direction: column;
    align-items: center;
    justify-content: center;
    gap: 44px;
    font-family: "Jost", sans-serif;
  }
  .card {
    position: relative;
    width: 630px;
    height: 360px;
    box-shadow: 0 10px 28px rgba(0,0,0,0.18);
    overflow: hidden;
  }

  /* Front: contact side */
  .card--front { background: var(--paper); }
  .front__band {
    position: absolute; left: 0; top: 0; bottom: 0;
    width: 30px; background: var(--brand-red);
  }
  .front__rule {
    position: absolute; left: 40px; top: 0; bottom: 0;
    width: 4px; background: var(--ink);
  }
  .brand-mark {
    position: absolute; left: 74px; top: 58px;
    display: flex; align-items: center; gap: 10px;
  }
  .brand-mark__dot {
    width: 40px; height: 40px; border-radius: 50%;
    background: var(--brand-red);
  }
  .brand-mark__name {
    font-family: "Montserrat", sans-serif;
    font-weight: 800; font-size: 19px; line-height: 1;
    color: var(--brand-red); text-transform: uppercase;
    width: 130px;
  }
  .holder {
    position: absolute; right: 50px; top: 118px; text-align: right;
  }
  .holder__name {
    font-family: "Jost", sans-serif; font-weight: 500;
    font-size: 27px; color: var(--ink); line-height: 1;
  }
  .holder__title { font-size: 13px; color: var(--muted); margin-top: 1px; }
  .front__divider {
    position: absolute; left: 150px; right: 40px; top: 176px;
    height: 2px; background: var(--brand-red);
  }
  .tagline {
    position: absolute; right: 40px; top: 188px; text-align: right;
  }
  .tagline__top {
    font-size: 19px; letter-spacing: 4px; color: var(--ink);
    text-transform: uppercase; line-height: 1.1;
  }
  .tagline__main {
    font-family: "Montserrat", sans-serif; font-weight: 800;
    font-size: 34px; color: var(--brand-red);
    text-transform: uppercase; line-height: 1;
  }
  .contact {
    position: absolute; left: 150px; top: 190px;
    list-style: none; font-size: 14px; color: var(--ink);
  }
  .contact__item { display: flex; align-items: center; gap: 8px; line-height: 1.55; }
  .contact__item svg { width: 11px; height: 11px; fill: var(--ink); flex: none; }

  /* Back: brand side */
  .card--back {
    background: var(--brand-red);
    display: flex; flex-direction: column; align-items: center;
    justify-content: center; color: var(--paper); text-align: center;
  }
  .back__dot {
    width: 110px; height: 110px; border-radius: 50%;
    background: var(--paper); margin-bottom: 18px;
  }
  .back__name {
    font-family: "Montserrat", sans-serif; font-weight: 800;
    font-size: 38px; text-transform: uppercase; line-height: 1;
  }
  .back__tagline {
    font-family: "Montserrat", sans-serif; font-weight: 600;
    font-size: 12px; text-transform: uppercase; letter-spacing: 0.3px;
    margin-top: 5px;
  }
  .back__web {
    display: flex; align-items: center; gap: 8px;
    font-size: 15px; letter-spacing: 0.5px; margin-top: 34px;
  }
  .back__web svg { width: 12px; height: 12px; }
</style>
</head>
<body>

  <section class="card card--front" aria-label="Business card, contact side">
    <div class="front__band"></div>
    <div class="front__rule"></div>

    <div class="brand-mark">
      <span class="brand-mark__dot"></span>
      <span class="brand-mark__name">Harborline Auto</span>
    </div>

    <div class="holder">
      <p class="holder__name">Person Name</p>
      <p class="holder__title">Chiefexecutive</p>
    </div>

    <div class="front__divider"></div>

    <ul class="contact">
      <li class="contact__item">
        <svg viewBox="0 0 24 24" aria-hidden="true"><path d="M6.6 10.8a15.1 15.1 0 0 0 6.6 6.6l2.2-2.2c.3-.3.7-.4 1-.2 1.1.4 2.3.6 3.6.6.6 0 1 .4 1 1V20c0 .6-.4 1-1 1A17 17 0 0 1 3 4c0-.6.4-1 1-1h3.5c.6 0 1 .4 1 1 0 1.3.2 2.5.6 3.6.1.3 0 .7-.2 1z"/></svg>
        (931) 555-0148, (629) 555-0173
      </li>
      <li class="contact__item">
        <svg viewBox="0 0 24 24" aria-hidden="true"><path d="M2 5h20v14H2z M3 6l9 7 9-7" fill="none" stroke="#1a1a1a" stroke-width="2.2"/></svg>
        harborlineautoxq@mailnest.example
      </li>
      <li class="contact__item">
        <svg viewBox="0 0 24 24" aria-hidden="true"><path d="M12 2a7 7 0 0 0-7 7c0 5.2 7 13 7 13s7-7.8 7-13a7 7 0 0 0-7-7zm0 9.5A2.5 2.5 0 1 1 12 6.5a2.5 2.5 0 0 1 0 5z"/></svg>
        2874 Cresthaven Road, Shelbyville, TN 37162
      </li>
    </ul>

    <div class="tagline" style="top:262px;">
      <p class="tagline__top">Car Dealer</p>
      <p class="tagline__main">Service</p>
    </div>
  </section>

  <section class="card card--back" aria-label="Business card, brand side">
    <span class="back__dot"></span>
    <p class="back__name">Harborline Auto</p>
    <p class="back__tagline">Car Dealer Customer Service</p>
    <p class="back__web">
      <svg viewBox="0 0 24 24" aria-hidden="true"><circle cx="12" cy="12" r="10" fill="none" stroke="#fff" stroke-width="2"/><path d="M2 12h20M12 2c3 3 3 17 0 20M12 2c-3 3-3 17 0 20" fill="none" stroke="#fff" stroke-width="1.6"/></svg>
      www.harborlineautoxq.net
    </p>
  </section>

</body>
</html>
```